Medical Marihuana Ziplock Bag Mockup Design

We seek skilled and professional designer for medical marihuana ziplock bag packaging design. We need a modern, minimal, clean Design with the name productname: Plomu - Endproduct will be a ziplock bag (see attachment) samples.
Product may but must not contain a cannabis leaf in Design7Logo

Target Market(s)

young audience

Industry/Entity Type

Medical

Logo Text

P L O M U

Font styles to use
Serif
Sans Serif

Colors
9bcb3c
abd037
cadf82
ffc214
fece3e
fee18a
6b449b
886aae
b8a6cd

Requirements
Nice to have
• Can but must not contain a minimal cannabis leaf as abstract sign

```html
<!DOCTYPE html>
<html lang="de">
<head>
<meta charset="utf-8">
<title>Plomu – Medical Marijuana Bag</title>
<link rel="stylesheet" href="https://fonts.googleapis.com/css2?family=Cormorant+Garamond:wght@500&family=Roboto+Slab:wght@300;600&family=Arimo:wght@700&family=Nunito+Sans:wght@600&display=swap">
<style>
  :root {
    --brand-green: #6a9a40;
    --pill-green: #8dc04a;
    --band-dark: #2d5227;
    --field-light: #86bd4f;
    --field-dark: #41703a;
    --cross-green: #5f9640;
    --leaf-pale: #c5e08a;
    --ink: #111111;
    --paper: #ffffff;
  }
  * { margin: 0; padding: 0; box-sizing: border-box; }
  html, body { width: 901px; height: 1200px; overflow: hidden; background: var(--paper); }
  .bag { position: relative; width: 901px; height: 1200px; overflow: hidden; background: var(--paper); }
  .top-band { position: absolute; left: 0; top: 0; width: 901px; height: 52px; background: var(--brand-green); }
  .leaf-art {
    position: absolute; left: 0; top: 0; width: 430px; height: 382px;
    background: radial-gradient(ellipse at 20% 15%, var(--leaf-pale) 0%, rgba(197,224,138,0.55) 40%, rgba(197,224,138,0) 72%);
  }
  .age-mark {
    position: absolute; right: 26px; top: 74px;
    font-family: "Nunito Sans", sans-serif; font-weight: 600; font-size: 38px; color: var(--brand-green);
  }
  .brand-name {
    position: absolute; left: 0; width: 901px; top: 218px; text-align: center;
    font-family: "Cormorant Garamond", serif; font-weight: 500; font-size: 172px; line-height: 1;
    letter-spacing: 2px; color: var(--brand-green);
  }
  .info-band { position: absolute; left: 0; top: 425px; width: 901px; height: 153px; background: var(--band-dark); }
  .category-pill {
    position: absolute; left: 191px; top: 390px; width: 519px; height: 70px; border-radius: 35px;
    background: var(--pill-green); box-shadow: 0 3px 6px rgba(0,0,0,0.3);
    font-family: "Roboto Slab", serif; font-weight: 600; font-size: 42px; line-height: 70px;
    color: var(--paper); text-align: center;
  }
  .origin-line, .content-line {
    position: absolute; left: 0; width: 901px; text-align: center;
    font-family: "Roboto Slab", serif; font-weight: 300;
  }
  .origin-line { top: 480px; font-size: 28px; color: var(--paper); }
  .content-line { top: 525px; font-size: 29px; color: var(--pill-green); }
  .divider { position: absolute; left: 0; top: 578px; width: 901px; height: 8px;
    background: linear-gradient(to bottom, #e6e6e6, #9a9a9a); }
  .lower-field { position: absolute; left: 0; top: 586px; width: 901px; height: 614px;
    background:
      linear-gradient(to right, rgba(255,255,255,0.06), rgba(255,255,255,0) 40%, rgba(255,255,255,0.08)),
      linear-gradient(to bottom, var(--field-light) 0%, #6aa144 45%, var(--field-dark) 100%); }
  .warning-frame { position: absolute; left: 125px; top: 588px; width: 650px; height: 471px;
    background: var(--ink); padding: 14px 14px 12px 16px; }
  .warning-panel { width: 100%; height: 100%; background: var(--paper);
    display: flex; flex-direction: column; justify-content: center; gap: 16px; text-align: center;
    font-family: "Arimo", sans-serif; font-weight: 700; font-size: 35px; line-height: 45px; color: var(--ink); }
  .net-weight { position: absolute; left: 50px; top: 1078px;
    font-family: "Nunito Sans", sans-serif; font-weight: 600; font-size: 66px; color: var(--paper); }
  .medical-cross { position: absolute; left: 654px; top: 1071px; width: 95px; height: 95px; }
  .strain-list { position: absolute; left: 785px; top: 1079px; list-style: none; }
  .strain-list li { display: flex; align-items: center; height: 30px;
    font-family: "Roboto Slab", serif; font-weight: 300; font-size: 14px; color: var(--paper); }
  .checkbox { width: 18px; height: 18px; border: 1.5px solid var(--ink); background: var(--paper); margin-right: 10px; }
</style>
</head>
<body>
<main class="bag">
  <div class="top-band"></div>
  <div class="leaf-art" role="img" aria-label="Large pale green hemp leaf illustration"></div>
  <div class="age-mark">18+</div>
  <h1 class="brand-name">PLOMU</h1>

  <div class="info-band"></div>
  <div class="category-pill">Medical Marijuana</div>
  <p class="origin-line">100% SCHWEIZER HANF</p>
  <p class="content-line">Product auf pflanzlicher Basis ohne Tabak</p>
  <div class="divider"></div>

  <div class="lower-field"></div>
  <section class="warning-frame">
    <div class="warning-panel">
      <p>Rauchen fügt Ihnen und den<br>Menschen in Ihrer Umgebung<br>erheblichen Schaden zu.</p>
      <p>Fumer nuit gravement à votre<br>santé et à celle de votre<br>entourage.</p>
      <p>Il fumo danneggia gravemente<br>te e chi ti sta intorno.</p>
    </div>
  </section>

  <div class="net-weight">10g</div>
  <svg class="medical-cross" viewBox="0 0 95 95" aria-hidden="true">
    <path fill="#5f9640" d="M31 0h33v31h31v33H64v31H31V64H0V31h31z"/>
  </svg>
  <ul class="strain-list">
    <li><span class="checkbox"></span>INDICA</li>
    <li><span class="checkbox"></span>SATIVA</li>
    <li><span class="checkbox"></span>HYBRID</li>
  </ul>
</main>
</body>
</html>
```